Business Card for a mobile physiotherapy company

I need a layout for a business card for a mobile physiotherapy company.
Slogan is "Mobile Physiotherapy - Your Road To Recovery"
Phone number is 867-555-0142
Email VardenTherapy@postnest.ca (subject to change with website)
Website www.VardenTherapy.ca
My name and credentials: Luke Varden Luke Varden, BSc(kin), MPT, CAFCI, IMS
Information maybe included: Direct Billing, Services including Physiotherapy, IMS, acupuncture
Maybe include facebook and instagram logos
One side with the logo clean and sharp
Other side with details, try not to look too busy, keep everything concise

```html
<!DOCTYPE html>
<html lang="en">
<head>
<meta charset="utf-8">
<title>Varden Therapy – Business Card</title>
<link href="https://fonts.googleapis.com/css2?family=Lato:wght@400;700&family=Tinos:wght@400;700&display=swap" rel="stylesheet">
<style>
  :root {
    --backdrop: #2b2b2d;
    --card-top: #1c1c1e;
    --card-bottom: #0b0b0c;
    --teal: #1d5f52;
    --blue: #34548f;
    --white: #f2f2f2;
    --rule: #4a4a4e;
  }
  * { box-sizing: border-box; margin: 0; padding: 0; }
  html, body { width: 1200px; height: 900px; overflow: hidden; }
  body {
    background: var(--backdrop);
    font-family: "Lato", Arial, sans-serif;
    color: var(--white);
    display: flex;
    flex-direction: column;
    align-items: center;
    justify-content: center;
    gap: 40px;
  }
  .card {
    position: relative;
    width: 600px;
    height: 343px;
    background: linear-gradient(160deg, var(--card-top), var(--card-bottom));
    box-shadow: 0 14px 30px rgba(0,0,0,.55);
    overflow: hidden;
  }
  .card__stripe {
    position: absolute;
    left: 0; right: 0; bottom: 0;
    height: 7px;
    background: linear-gradient(90deg, var(--teal) 0%, var(--teal) 40%, var(--blue) 60%, var(--blue) 100%);
  }

  /* Front */
  .front {
    display: flex;
    flex-direction: column;
    align-items: center;
    justify-content: center;
    padding-bottom: 10px;
  }
  .brand-name {
    font-family: "Lato", Arial, sans-serif;
    font-weight: 700;
    font-size: 44px;
    letter-spacing: 6px;
    color: var(--teal);
    line-height: 1;
    display: flex;
    align-items: center;
    gap: 14px;
  }
  .brand-name__mark {
    width: 14px; height: 14px;
    background: var(--blue);
  }
  .social-row {
    display: flex;
    align-items: center;
    gap: 8px;
    margin-top: 26px;
  }
  .social-row__rule { width: 96px; height: 1px; background: var(--rule); }
  .social-row__dot { width: 16px; height: 16px; border-radius: 50%; background: var(--white); }
  .tagline {
    margin-top: 16px;
    font-size: 14px;
    letter-spacing: .6px;
    text-transform: uppercase;
  }

  /* Back */
  .back { padding: 0 44px; }
  .back__main {
    position: absolute;
    top: 95px; left: 44px; right: 30px;
    display: flex;
    align-items: flex-start;
  }
  .person { width: 250px; text-align: right; padding-right: 22px; font-family: "Tinos", "Times New Roman", serif; }
  .person__name { color: var(--teal); font-weight: 700; font-size: 20px; letter-spacing: .5px; text-transform: uppercase; }
  .person__creds { font-size: 15px; margin-top: 2px; letter-spacing: .3px; }
  .divider { width: 1px; height: 92px; background: var(--rule); margin-top: 26px; }
  .contact { list-style: none; padding-left: 18px; margin-top: 34px; font-size: 16px; }
  .contact li { display: flex; align-items: center; gap: 8px; line-height: 22px; }
  .contact svg { width: 13px; height: 13px; fill: var(--blue); flex: none; }
  .services {
    position: absolute;
    left: 44px; bottom: 52px;
    display: flex;
    align-items: center;
    gap: 12px;
    font-size: 17px;
  }
  .services__dot { width: 6px; height: 6px; border-radius: 50%; background: var(--blue); }
</style>
</head>
<body>

  <section class="card front">
    <div class="brand-name"><span class="brand-name__mark"></span>VARDEN THERAPY</div>
    <div class="social-row">
      <span class="social-row__rule"></span>
      <span class="social-row__dot"></span>
      <span class="social-row__dot"></span>
      <span class="social-row__rule"></span>
    </div>
    <p class="tagline">Mobile Physiotherapy Your Road to Recovery</p>
    <span class="card__stripe"></span>
  </section>

  <section class="card back">
    <div class="back__main">
      <div class="person">
        <p class="person__name">Luke Varden</p>
        <p class="person__creds">BSC(KIN), MPT, CAFCI, IMS</p>
      </div>
      <span class="divider"></span>
      <ul class="contact">
        <li>
          <svg viewBox="0 0 16 16" aria-hidden="true"><path d="M3 1h3l1.5 4-2 1.3a9 9 0 0 0 4.2 4.2L11 8.5l4 1.5v3a2 2 0 0 1-2 2A13 13 0 0 1 1 3a2 2 0 0 1 2-2z"/></svg>
          867-555-0142
        </li>
        <li>
          <svg viewBox="0 0 16 16" aria-hidden="true"><path d="M1 3h14v10H1z M1 3l7 6 7-6" stroke="#1c1c1e" stroke-width="1.2"/></svg>
          VardenTherapy@postnest.ca
        </li>
        <li>
          <svg viewBox="0 0 16 16" aria-hidden="true"><circle cx="8" cy="8" r="7"/><path d="M1 8h14M8 1c3 3 3 11 0 14M8 1c-3 3-3 11 0 14" stroke="#1c1c1e" stroke-width="1" fill="none"/></svg>
          www.VardenTherapy.ca
        </li>
      </ul>
    </div>
    <div class="services">
      <span>Direct Billing</span><span class="services__dot"></span>
      <span>Physiotherapy</span><span class="services__dot"></span>
      <span>IMS</span><span class="services__dot"></span>
      <span>acupuncture</span>
    </div>
    <span class="card__stripe"></span>
  </section>

</body>
</html>
```